Founder / concept developer needs business card // Consultant needs VCARD

I need a business card for me as a founding consultant in Berlin. I advise entrepreneurs, especially in the design of business ideas, business plans or financing applications. More information about this in the annexes. My USP: I design / structure complex ideas and projects convincingly so that my client is successful. I want to communicate professionalism, effectiveness and clarity. Colors like from the range BLACK-GRAY-GREEN. I am 27 years old, I have studied business for 7 years. Attachments: - Business card design (only idea, do not focus on it) - Website screenshot (only idea, do not focus on it)

Target Market(s)

Target group: Founder (20-50 yrs, m / w, needy, in "break-up phase") and CONTRACTOR / "financier" (30-55 yrs, m / w, often public service "routine-oriented"). The foundations are in quite different industries: digital, craft, tourism, retail, services, etc. Almost all German.

Industry/Entity Type

Consultant

Contact Information for Business Card

Lukas Brennwald
M. Sc., International Business Administration
Gründungsberater, Konzeptentwickler
www.kelvoran-mitrel.de
Postfach-Zugang@kelvoran.de
Tel. 0481 294 3172

Colors

Designer to choose colors to be used in the design.

Requirements
Must have
• Professionalism, persuasiveness, clarity
Nice to have
• memorability
Should not have
• Schnörkelei

```html
<!DOCTYPE html>
<html lang="de">
<head>
<meta charset="utf-8">
<title>Lukas Brennwald – Visitenkarte</title>
<link href="https://fonts.googleapis.com/css2?family=Open+Sans:wght@400;600;700&display=swap" rel="stylesheet">
<style>
  :root {
    --page-bg: #ecebe8;
    --card-white: #ffffff;
    --card-dark: #2a2d31;
    --accent-green: #3aa335;
    --back-green: #40a63b;
    --back-green-light: #4cb046;
    --cube-light: #8fcf9a;
    --cube-mid: #3e9f3a;
    --cube-dark: #2b7a2b;
    --bracket: #1f2225;
    --text-light: #ffffff;
  }
  * { box-sizing: border-box; margin: 0; padding: 0; }
  html, body { width: 1200px; height: 900px; overflow: hidden; }
  body {
    background: var(--page-bg);
    font-family: "Open Sans", Arial, sans-serif;
    position: relative;
  }
  .card {
    position: absolute;
    width: 588px;
    height: 360px;
    overflow: hidden;
    box-shadow: 0 6px 18px rgba(0,0,0,0.18);
  }
  .card-front { left: 178px; top: 74px; background: var(--card-white); }
  .card-back {
    left: 388px; top: 505px; width: 567px; height: 352px;
    background: radial-gradient(circle at 50% 45%, var(--back-green-light), var(--back-green) 75%);
  }
  .front-shape { position: absolute; inset: 0; }
  .emblem { position: absolute; }
  .emblem-front { left: 232px; top: 36px; width: 150px; height: 150px; }
  .emblem-back { left: 188px; top: 78px; width: 190px; height: 190px; }
  .emblem-frame { position: absolute; inset: 0; width: 100%; height: 100%; }
  .emblem-art {
    position: absolute; inset: 14%;
    border-radius: 8px;
    background: linear-gradient(135deg, var(--cube-light) 0%, var(--cube-mid) 55%, var(--cube-dark) 100%);
  }
  .holder {
    position: absolute; left: 0; top: 254px; width: 264px;
    text-align: right; color: var(--text-light);
  }
  .holder-name { font-size: 19px; font-weight: 600; line-height: 24px; letter-spacing: 0.2px; }
  .holder-role { font-size: 15px; font-weight: 400; line-height: 20px; }
  .contact-list {
    position: absolute; left: 284px; top: 247px;
    list-style: none; color: var(--text-light);
    font-size: 15px; line-height: 21.5px;
  }
  .contact-item { display: flex; align-items: center; gap: 11px; }
  .contact-icon { width: 12px; height: 12px; fill: var(--text-light); flex: none; }
  .address {
    position: absolute; left: 90px; top: 318px;
    color: var(--text-light); font-size: 15px; line-height: 22px;
  }
</style>
</head>
<body>

<section class="card card-front" aria-label="Visitenkarte Vorderseite">
  <svg class="front-shape" viewBox="0 0 588 360" preserveAspectRatio="none" aria-hidden="true">
    <path d="M0,160 Q294,300 588,160 L588,360 L0,360 Z" fill="var(--card-dark)"/>
    <path d="M0,160 Q294,300 588,160" fill="none" stroke="var(--accent-green)" stroke-width="3"/>
  </svg>

  <div class="emblem emblem-front">
    <svg class="emblem-frame" viewBox="0 0 100 100" aria-hidden="true">
      <path d="M1,14 V1 H14 M86,1 H99 V14 M99,86 V99 H86 M14,99 H1 V86" fill="none" stroke="var(--bracket)" stroke-width="1.3"/>
    </svg>
    <div class="emblem-art" role="img" aria-label="Illustration eines grünen Zauberwürfels"></div>
  </div>

  <div class="holder">
    <p class="holder-name">Lukas Brennwald</p>
    <p class="holder-role">Managing Director</p>
  </div>

  <ul class="contact-list">
    <li class="contact-item">
      <svg class="contact-icon" viewBox="0 0 24 24" aria-hidden="true"><path d="M6.6 10.8a15.1 15.1 0 0 0 6.6 6.6l2.2-2.2a1 1 0 0 1 1-.25 11.4 11.4 0 0 0 3.6.57 1 1 0 0 1 1 1V20a1 1 0 0 1-1 1A17 17 0 0 1 3 4a1 1 0 0 1 1-1h3.5a1 1 0 0 1 1 1c0 1.25.2 2.45.57 3.57a1 1 0 0 1-.25 1z"/></svg>
      <span>0481 294 3172</span>
    </li>
    <li class="contact-item">
      <svg class="contact-icon" viewBox="0 0 24 24" aria-hidden="true"><path d="M2 5h20v14H2z M3.5 6.5 12 12.5l8.5-6" fill="var(--text-light)" stroke="var(--card-dark)" stroke-width="1.6"/></svg>
      <span>Postfach-Zugang@kelvoran.de</span>
    </li>
    <li class="contact-item">
      <svg class="contact-icon" viewBox="0 0 24 24" aria-hidden="true"><circle cx="12" cy="12" r="10"/><path d="M2 12h20M12 2c3 3 3 17 0 20M12 2c-3 3-3 17 0 20M4 7h16M4 17h16" fill="none" stroke="var(--card-dark)" stroke-width="1.4"/></svg>
      <span>www.kelvoran-mitrel.de</span>
    </li>
  </ul>

  <p class="address">12345, Address Goes Here, Country Name here, 123456.</p>
</section>

<section class="card card-back" aria-label="Visitenkarte Rückseite">
  <div class="emblem emblem-back">
    <svg class="emblem-frame" viewBox="0 0 100 100" aria-hidden="true">
      <path d="M1,14 V1 H14 M86,1 H99 V14 M99,86 V99 H86 M14,99 H1 V86" fill="none" stroke="var(--bracket)" stroke-width="1.1"/>
    </svg>
    <div class="emblem-art" role="img" aria-label="Illustration eines grünen Zauberwürfels"></div>
  </div>
</section>

</body>
</html>
```